Design a homepage graphic to show a system journey

We have a software package for parents to update student information and manage school excursions we have attached a concept we like but are open to other ideas so long as they fit the following criteria.
1 It needs to be landscape across the page
2. They are showing a series of processes, each step has its own colour, see below
2.1 The first process is a parent updating their own and students information and approving excursions
2.2 The school then creates and manages the excursion this includes a compliance component
2.3 The school conducts the activity it should show some activity type pictures
2.4 Students return safely to school
3 There can be text boxes within the image to clarify functionality
4. The picture should make anyone watching it understand there is a series of
linked processes the system provides i.e. a journey
There should be the ability to click on each component to link to a specific part of the pager lower down, e.g if the person wanted to look at the school part by clicking on the school it would take them to more information, that information already exists so is not required.
Please review the attached concept diagram and use this a potential guide.
Schools
1 page

```html
<!DOCTYPE html>
<html lang="en">
<head>
<meta charset="utf-8">
<title>School Excursion Journey</title>
<link href="https://fonts.googleapis.com/css2?family=Poppins:wght@600&family=Roboto:wght@400&display=swap" rel="stylesheet">
<style>
  :root{
    --green:#7dc11d;
    --teal:#3dbb9c;
    --cyan:#26a9cd;
    --blue:#3a78c9;
    --purple:#5b55b0;
    --line:#4a4a4a;
    --body:#3c3c3c;
    --bg-a:#f4f4f4;
    --bg-b:#ececec;
  }
  html,body{margin:0;padding:0;overflow:hidden;}
  .canvas{
    position:relative;width:1200px;height:677px;overflow:hidden;
    font-family:"Roboto",Arial,sans-serif;color:var(--body);
  }
  .backdrop{
    position:absolute;inset:0;
    background:
      radial-gradient(ellipse at 35% 35%, #ebe3e3 0%, transparent 45%),
      radial-gradient(ellipse at 75% 40%, #eceae2 0%, transparent 45%),
      linear-gradient(180deg,var(--bg-a) 0%,var(--bg-b) 100%);
  }
  .journey{position:absolute;left:0;top:0;}
  .step-note{position:absolute;text-decoration:none;color:inherit;}
  .step-title{
    font-family:"Poppins",Arial,sans-serif;font-weight:600;
    font-size:13px;line-height:16px;margin:0 0 6px;text-transform:uppercase;white-space:nowrap;
  }
  .step-text{font-size:13px;line-height:22.4px;margin:0;}
  .parent .step-title{color:var(--green);}
  .students .step-title{color:var(--teal);}
  .excursion .step-title{color:var(--cyan);}
  .activity .step-title{color:var(--blue);}
  .return .step-title{color:var(--purple);}
  .activity-body{display:flex;gap:12px;align-items:flex-start;margin-top:10px;}
  .activity-photo{
    width:69px;height:64px;border-radius:4px;flex:none;margin-left:2px;
    background:linear-gradient(160deg,#9a3b33 0%,#c9a07c 45%,#7d8a9a 100%);
    box-shadow:0 2px 5px rgba(0,0,0,.3);border:2px solid #fff;box-sizing:border-box;
  }
  .activity .step-text{margin-top:-6px;}
</style>
</head>
<body>
<div class="canvas">
  <div class="backdrop" role="img" aria-label="Faded background photo of children jumping happily"></div>

  <svg class="journey" width="1200" height="677" viewBox="0 0 1200 677">
    <g fill="none" stroke="var(--line)" stroke-width="1.5">
      <!-- timeline segments -->
      <line x1="59" y1="335" x2="131" y2="335"/>
      <line x1="237" y1="335" x2="320" y2="335"/>
      <line x1="426" y1="335" x2="508" y2="335"/>
      <line x1="614" y1="335" x2="697" y2="335"/>
      <line x1="803" y1="335" x2="885" y2="335"/>
      <line x1="991" y1="335" x2="1078" y2="335"/>
      <!-- arcs -->
      <path d="M131 335 A53 53 0 0 1 237 335" stroke-width="1"/>
      <path d="M320 335 A53 53 0 0 0 426 335" stroke-width="1"/>
      <path d="M508 335 A53 53 0 0 1 614 335" stroke-width="1"/>
      <path d="M697 335 A53 53 0 0 0 803 335" stroke-width="1"/>
      <path d="M885 335 A53 53 0 0 1 991 335" stroke-width="1"/>
    </g>
    <!-- line ends -->
    <circle cx="54" cy="335" r="5.5" fill="#fff" stroke="#5a5a5a" stroke-width="2.5"/>
    <circle cx="1084" cy="335" r="5.5" fill="#fff" stroke="#5a5a5a" stroke-width="2.5"/>
    <!-- arc dots -->
    <g fill="#555">
      <circle cx="184" cy="282" r="3.5"/>
      <circle cx="373" cy="389" r="3.5"/>
      <circle cx="561" cy="282" r="3.5"/>
      <circle cx="750" cy="389" r="3.5"/>
      <circle cx="938" cy="282" r="3.5"/>
    </g>

    <!-- dotted connectors -->
    <g stroke="#555" stroke-width="3" stroke-linecap="round" stroke-dasharray="0 6.2">
      <line x1="184" y1="181" x2="184" y2="245"/>
      <line x1="373" y1="440" x2="373" y2="503"/>
      <line x1="561" y1="181" x2="561" y2="245"/>
      <line x1="750" y1="441" x2="750" y2="504"/>
      <line x1="938" y1="181" x2="938" y2="245"/>
    </g>
    <g>
      <circle cx="184" cy="169" r="5.5" fill="#fff" stroke="var(--green)" stroke-width="3"/>
      <circle cx="184" cy="253" r="3.5" fill="var(--green)"/>
      <circle cx="373" cy="427" r="5.5" fill="#fff" stroke="var(--teal)" stroke-width="3"/>
      <circle cx="373" cy="511" r="3.5" fill="var(--teal)"/>
      <circle cx="561" cy="169" r="5.5" fill="#fff" stroke="var(--cyan)" stroke-width="3"/>
      <circle cx="561" cy="253" r="3.5" fill="var(--cyan)"/>
      <circle cx="750" cy="428" r="5.5" fill="#fff" stroke="var(--blue)" stroke-width="3"/>
      <circle cx="750" cy="512" r="3.5" fill="var(--blue)"/>
      <circle cx="938" cy="169" r="5.5" fill="#fff" stroke="var(--purple)" stroke-width="3"/>
      <circle cx="938" cy="253" r="3.5" fill="var(--purple)"/>
    </g>

    <!-- step badges -->
    <a href="#parents">
      <circle cx="184" cy="337" r="45" fill="var(--green)" opacity=".35"/>
      <circle cx="184" cy="337" r="40" fill="#5f9a12"/>
      <circle cx="184" cy="335" r="39" fill="var(--green)" role="img" aria-label="Icon of a parent group"/>
    </a>
    <a href="#students">
      <circle cx="373" cy="337" r="45" fill="var(--teal)" opacity=".35"/>
      <circle cx="373" cy="337" r="40" fill="#2a9a7e"/>
      <circle cx="373" cy="335" r="39" fill="var(--teal)" role="img" aria-label="Icon of two students"/>
    </a>
    <a href="#excursion">
      <circle cx="561" cy="337" r="45" fill="var(--cyan)" opacity=".35"/>
      <circle cx="561" cy="337" r="40" fill="#1b88a8"/>
      <circle cx="561" cy="335" r="39" fill="var(--cyan)" role="img" aria-label="Icon of a staff member with a compliance shield"/>
    </a>
    <a href="#activity">
      <circle cx="750" cy="337" r="45" fill="var(--blue)" opacity=".35"/>
      <circle cx="750" cy="337" r="40" fill="#2b5ea3"/>
      <circle cx="750" cy="335" r="39" fill="var(--blue)" role="img" aria-label="Icon of children dancing"/>
    </a>
    <a href="#return">
      <circle cx="938" cy="337" r="45" fill="var(--purple)" opacity=".35"/>
      <circle cx="938" cy="337" r="40" fill="#443f91"/>
      <circle cx="938" cy="335" r="39" fill="var(--purple)" role="img" aria-label="Icon of a student with a backpack"/>
    </a>
  </svg>

  <a class="step-note parent" href="#parents" style="left:204px;top:165px;">
    <p class="step-title">Parent Information</p>
    <p class="step-text">Lorem ipsum dolor sit amet<br>consectetur adipiscing elitd<br>sed dot eiusmod tempoed.</p>
  </a>
  <a class="step-note students" href="#students" style="left:394px;top:421px;">
    <p class="step-title">Students Information</p>
    <p class="step-text">Lorem ipsum dolor sit amet<br>consectetur adipiscing elitd<br>sed dot eiusmod tempoed.</p>
  </a>
  <a class="step-note excursion" href="#excursion" style="left:582px;top:165px;">
    <p class="step-title">Approving Excursion</p>
    <p class="step-text">Lorem ipsum dolor sit amet<br>consectetur adipiscing elitd<br>sed dot eiusmod tempoed.</p>
  </a>
  <a class="step-note activity" href="#activity" style="left:771px;top:422px;">
    <p class="step-title">School Conducts Activity</p>
    <div class="activity-body">
      <div class="activity-photo" role="img" aria-label="Photo of children jumping during a school activity"></div>
      <p class="step-text">Lorem ipsum dolor<br>sit amet consectetur<br>adipiscing elitd sed</p>
    </div>
  </a>
  <a class="step-note return" href="#return" style="left:957px;top:165px;">
    <p class="step-title">Students Return to School</p>
    <p class="step-text">Lorem ipsum dolor sit amet<br>consectetur adipiscing elitd<br>sed dot eiusmod tempoed.</p>
  </a>
</div>
</body>
</html>
```